Harvest Gateway Fellowship Ministries needs a fresh new web design

We are an up and coming multicultural church that aims to bring people into a life changing encounter with God. We need a fresh and inviting website in order to increase our internet presence and make us easier to connect with.
Here are some of the basic requirements for the site:
• Clearly displayed address, service times, and contact info
• A staff profile page
• An area for a calendar with upcoming events and their details
• Social media buttons
• Group pages for the different ministries (youth, children’s church, men, etc…)
• An area for donations and eCommerce
• A resources page for assorted media (podcasts, sermons, videos, etc.…)
• An area for prayer requests.

```html
<!DOCTYPE html>
<html lang="en">
<head>
<meta charset="utf-8">
<title>Harvest Gateway Fellowship Ministries</title>
<link href="https://fonts.googleapis.com/css2?family=Gelasio:wght@400;700&family=Open+Sans:wght@400;600;700&display=swap" rel="stylesheet">
<style>
:root{
  --gold:#b8922a;
  --gold-light:#f3c72d;
  --gold-pale:#fbe58c;
  --brown:#3e3218;
  --brown-dark:#2f2410;
  --navy:#0d5286;
  --navy-field:#1768a4;
  --ink:#444;
  --heading:#3a2e12;
  --muted:#777;
  --white:#fff;
}
*{margin:0;padding:0;box-sizing:border-box}
html,body{width:680px;height:1200px;overflow:hidden;background:var(--white)}
body{position:relative;font-family:"Open Sans",Arial,sans-serif;color:var(--ink)}
.abs{position:absolute}

/* header */
.header{left:0;top:0;width:680px;height:310px;background:linear-gradient(180deg,#f7d245 0%,#f2be1f 40%,#eeb015 70%,#f4c52a 100%)}
.brand{left:0;top:34px;width:680px;font-family:"Gelasio",Georgia,serif;font-size:11px;color:var(--brown);font-weight:700;display:flex;justify-content:center;align-items:center;gap:6px}
.brand-dot{width:22px;height:22px;border-radius:50%;background:var(--brown)}
.hero-photo{left:103px;top:102px;width:319px;height:158px;background:linear-gradient(135deg,#d8d3cc,#8a6b5a 55%,#c9a9a1)}
.hero-panel{left:422px;top:102px;width:155px;height:158px;background:var(--brown)}
.hero-title{left:435px;top:130px;width:140px;font-family:"Gelasio",Georgia,serif;font-weight:400;font-size:19px;line-height:17px;color:var(--white)}
.dots{left:436px;top:243px;display:flex;gap:3px}
.dots span{width:8px;height:8px;border-radius:50%;background:#6b5a2c}
.dots span:first-child{background:var(--gold-light)}
.nav{left:103px;top:260px;width:474px;height:32px;background:linear-gradient(180deg,#f3c93a,#d9a514);box-shadow:0 6px 6px -3px rgba(80,50,0,.45);display:flex;padding-left:10px}
.nav a{font-family:"Gelasio",Georgia,serif;font-size:9px;color:var(--white);text-decoration:none;padding:0 10px;line-height:32px;border-right:1px solid rgba(160,110,0,.45)}

/* welcome */
.welcome-h{left:103px;top:328px;font-family:"Gelasio",Georgia,serif;font-weight:400;font-size:15px;color:var(--heading)}
.welcome-p{left:103px;top:356px;width:294px;font-size:6.6px;line-height:12px;color:var(--ink)}
.welcome-p p{margin-bottom:7px}
.welcome-sign{left:103px;top:468px;font-family:"Gelasio",Georgia,serif;font-size:9px;color:#5a4a10}

.bar{height:27px;background:var(--gold);color:var(--white);font-family:"Gelasio",Georgia,serif;font-size:12px;line-height:27px;padding-left:8px}
.group-bar{left:103px;top:498px;width:294px}
.select{left:298px;top:503px;width:94px;height:17px;background:var(--brown);color:var(--gold-light);font-family:"Gelasio",Georgia,serif;font-size:6px;line-height:17px;padding-left:5px}
.select::after{content:"";position:absolute;right:6px;top:6px;width:4px;height:4px;border-right:1px solid var(--gold-light);border-bottom:1px solid var(--gold-light);transform:rotate(45deg)}
.group-tile{top:530px;width:94px;height:70px;background:linear-gradient(160deg,#c9b49a,#7a5a3a 60%,#3b2a18)}
.group-tile span{position:absolute;left:3px;bottom:4px;font-family:"Gelasio",Georgia,serif;font-size:5.5px;color:var(--white)}
.group-tile i{position:absolute;right:4px;bottom:3px;width:8px;height:8px;border-radius:50%;background:var(--white)}

/* staff */
.staff-bar{left:103px;top:626px;width:294px}
.staff-photo{left:103px;top:670px;width:64px;height:85px;background:linear-gradient(180deg,#ececec,#4a4040 60%,#2d2626)}
.staff-role{left:103px;top:764px;width:64px;text-align:center;font-family:"Gelasio",Georgia,serif;font-style:italic;font-size:8px;color:#666;line-height:10px}
.staff-role b{display:block;font-family:"Open Sans",Arial,sans-serif;font-size:6.5px;color:var(--gold);font-weight:400}
.staff-name{left:182px;top:664px;font-family:"Gelasio",Georgia,serif;font-size:8.5px;color:var(--gold)}
.staff-bio{left:182px;top:681px;width:222px;font-size:6.5px;line-height:12px;color:var(--muted)}
.staff-bio p{margin-bottom:12px}

.testimonials{left:103px;top:814px;width:294px;height:80px;background:var(--gold);padding:6px 8px}
.testimonials h3{font-family:"Gelasio",Georgia,serif;font-weight:400;font-size:11.5px;color:var(--white)}
.quote-mark{position:absolute;left:5px;top:22px;font-family:"Gelasio",Georgia,serif;font-size:24px;line-height:24px;color:var(--gold-light);font-weight:700}
.testimonials p{position:absolute;left:10px;top:40px;width:280px;font-style:italic;font-size:6.5px;line-height:10px;color:var(--white)}
.arrows{position:absolute;right:8px;top:6px;font-size:9px;color:var(--gold-light);font-weight:700}

/* calendar */
.calendar{left:423px;top:334px;width:152px;height:266px;background:#e2b530;border:1px solid #c99a1f}
.cal-head{height:20px;background:var(--brown);color:var(--gold-light);font-size:7px;font-weight:700;text-align:center;line-height:20px;position:relative}
.cal-head i{position:absolute;top:6px;width:8px;height:8px;background:var(--white)}
.cal-head i.prev{left:6px}.cal-head i.next{right:6px}
.cal-head i::after{content:"";position:absolute;top:2px;border:2px solid transparent}
.cal-head i.prev::after{left:1px;border-right:3px solid var(--brown)}
.cal-head i.next::after{left:3px;border-left:3px solid var(--brown)}
.cal-table{width:146px;margin:8px 3px 0;border-collapse:collapse;font-size:5.2px;color:#5a4512;text-align:center}
.cal-table th{font-weight:400;height:14px}
.cal-table td{height:18px;border-top:1px solid rgba(150,110,20,.35)}
.events-h{position:absolute;left:10px;top:148px;font-size:6px;font-weight:700;color:var(--brown)}
.event{position:absolute;left:10px;width:132px;display:flex;gap:5px;align-items:flex-start}
.event .thumb{flex:0 0 43px;height:31px;background:linear-gradient(135deg,#d8d0c0,#4a3a2a)}
.event p{width:84px;font-size:5.2px;line-height:7.5px;color:var(--white)}
.event-rule{position:absolute;left:10px;top:196px;width:132px;height:1px;background:rgba(120,85,10,.45)}
.read-btn{position:absolute;right:8px;bottom:7px;background:var(--brown);color:var(--white);font-size:5.5px;font-weight:600;padding:5px 7px}

/* prayer */
.prayer{left:423px;top:619px;width:152px;height:275px;background:var(--navy);padding:10px 11px}
.prayer h3{font-family:"Gelasio",Georgia,serif;font-weight:400;font-size:13px;color:var(--gold-light);margin-bottom:8px}
.prayer label{display:block;font-family:"Gelasio",Georgia,serif;font-size:6px;color:var(--white);margin-bottom:5px}
.prayer .field{height:16px;background:var(--navy-field);margin-bottom:13px}
.prayer .field.tall{height:39px;margin-bottom:10px}
.submit{position:absolute;right:8px;bottom:9px;background:#e2a818;color:var(--white);font-size:6.5px;font-weight:700;padding:4px 7px}

/* quote and media */
.motto{left:0;top:912px;width:680px;text-align:center;font-family:"Gelasio",Georgia,serif;font-size:14px;color:var(--heading)}
.media{top:942px;width:155px;height:69px}
.media .label{position:absolute;left:20px;top:42px;font-family:"Gelasio",Georgia,serif;font-size:11.5px;color:var(--white)}
.media .ico{position:absolute;left:8px;top:45px;width:9px;height:11px;border:1.5px solid var(--white);border-radius:2px}
.media .more{position:absolute;right:5px;top:43px;background:var(--navy);color:var(--white);font-family:"Gelasio",Georgia,serif;font-size:6px;padding:4px 6px}
.m1{left:103px;background:linear-gradient(135deg,#4a4a4a,#1d1d1d 55%,#5fc0c0)}
.m2{left:262px;background:linear-gradient(135deg,#2a2826,#5a4a3a 50%,#1f1c1a)}
.m3{left:422px;background:linear-gradient(180deg,#d7a45a,#8a4a25 70%,#3a1f10)}

/* footer */
.footer{left:0;top:1037px;width:680px;height:163px;background:var(--brown-dark)}
.f-h{font-size:6.5px;font-weight:700;color:var(--gold-light)}
.f-list{font-size:6.5px;line-height:12px;color:var(--white);list-style:none}
.f-contact div{display:flex;align-items:center;gap:8px;font-size:6.5px;color:var(--white);height:19px}
.f-contact svg{width:10px;height:10px}
.social{display:flex;gap:3px}
.social span{width:15px;height:15px;border-radius:50%;border:1px solid #777;background:#3d3220}
.cards{display:flex;gap:4px}
.cards span{width:24px;height:13px;background:var(--white);border-radius:2px}
.donate-pill{width:79px;height:13px;border-radius:7px;background:#f1b52b;color:var(--brown-dark);font-size:6px;font-weight:700;text-align:center;line-height:13px}
.f-legal{left:0;top:1163px;width:680px;text-align:center;font-size:6.5px;line-height:14px;color:var(--white)}
</style>
</head>
<body>

<header class="abs header">
  <div class="abs brand"><span class="brand-dot"></span>Harvest Gateway Fellowship Ministries</div>
  <div class="abs hero-photo" role="img" aria-label="Photo of church leaders standing together in a classroom"></div>
  <div class="abs hero-panel"></div>
  <h1 class="abs hero-title">Harvest Gateway Fellowship Ministries</h1>
  <div class="abs dots"><span></span><span></span><span></span><span></span></div>
  <nav class="abs nav">
    <a>Home</a><a>About Us</a><a>Events</a><a>Prayer Request</a><a>Donate</a><a>Contact Us</a>
  </nav>
</header>

<h2 class="abs welcome-h">Welcome to HGFM</h2>
<div class="abs welcome-p">
  <p>Welcome to Harvest Gateway Fellowship Ministries, a place where we can come together and fellowship. HGFM is located in Millbrook, New York and we would love to have you worship with us. We believe God is doing something extraordinary through our church and would like for you to be a part. Please prayerfully consider our church as a place you would like to worship and fellowship with us as we continue to grow.</p>
  <p>As you venture on our website please feel free to contact us through email, phone, or leave a prayer request for us to pray on your behalf. Please take a minute and look at our upcoming events.</p>
</div>
<div class="abs welcome-sign">We hope you will visit us real soon.</div>

<div class="abs bar group-bar">Group</div>
<div class="abs select">Children's Church</div>
<div class="abs group-tile" style="left:103px" role="img" aria-label="Photo of children in church"><span>Childrens In church</span><i></i></div>
<div class="abs group-tile" style="left:203px" role="img" aria-label="Photo of children in church"><span>Childrens In church</span><i></i></div>
<div class="abs group-tile" style="left:303px" role="img" aria-label="Photo of children in church"><span>Childrens In church</span><i></i></div>

<div class="abs bar staff-bar">Our Staffs</div>
<div class="abs staff-photo" role="img" aria-label="Portrait of the minister holding a Bible"></div>
<div class="abs staff-role">Minister<b>Marisol Grant</b></div>
<div class="abs staff-name">Marisol Grant-Minister, Sunday School Teacher</div>
<div class="abs staff-bio">
  <p>Marisol Grant is the co-founder of Harvest Gateway Fellowship Ministries. A native of Panama who accepted the Lord at the age of 19, she is a dedicated educator in both the secular and Christian community, helping children and adults with special needs acquire and achieve life long skills.</p>
  <p>Definitely, without the grace and help of the almighty God this work would not be possible. The goal of the educational ministry is to help children and young adults build their educational skills and spiritual walk with Christ.</p>
</div>

<div class="abs testimonials">
  <h3>Testimonials</h3>
  <span class="arrows">&lsaquo;&rsaquo;</span>
  <span class="quote-mark">&ldquo;</span>
  <p>Lorem Ipsum is simply dummy text of the printing and typesetting industry. Lorem Ipsum has been the industry's standard dummy text ever since the 1500s, when an unknown printer took a galley of type and scrambled it to make a type specimen book</p>
</div>

<aside class="abs calendar">
  <div class="cal-head"><i class="prev"></i>Jun 2014<i class="next"></i></div>
  <table class="cal-table">
    <tr><th>Mon</th><th>Tue</th><th>Wed</th><th>Thu</th><th>Fri</th><th>Sat</th><th>Sun</th></tr>
    <tr><td>27</td><td>28</td><td>29</td><td>01</td><td>02</td><td>03</td><td>04</td></tr>
    <tr><td>05</td><td>06</td><td>07</td><td>08</td><td>09</td><td>10</td><td>11</td></tr>
    <tr><td>12</td><td>13</td><td>14</td><td>15</td><td>16</td><td>17</td><td>18</td></tr>
    <tr><td>19</td><td>20</td><td>21</td><td>22</td><td>23</td><td>24</td><td>25</td></tr>
    <tr><td>26</td><td>27</td><td>28</td><td>29</td><td>30</td><td>31</td><td></td></tr>
  </table>
  <div class="events-h">Events Calendar</div>
  <div class="event" style="top:160px"><div class="thumb" role="img" aria-label="Event photo"></div><p>Lorem Ipsum is simply dummy text of the printing and typesetting industry.</p></div>
  <div class="event-rule"></div>
  <div class="event" style="top:206px"><div class="thumb" role="img" aria-label="Event photo"></div><p>Lorem Ipsum is simply dummy text of the printing and typesetting industry.</p></div>
  <div class="read-btn">Read More</div>
</aside>

<form class="abs prayer">
  <h3>Prayer Requests</h3>
  <label>Your Name:</label><div class="field"></div>
  <label>Your Email Address:</label><div class="field"></div>
  <label>Prayer Title:</label><div class="field"></div>
  <label>Prayer Topic:</label><div class="field"></div>
  <label>Your Prayer Request:</label><div class="field tall"></div>
  <div class="submit">SUBMIT</div>
</form>

<div class="abs motto">"No limits, No Boundaries, but increase in Jesus name"</div>

<div class="abs media m1" role="img" aria-label="Microphone photo for podcasts"><span class="ico"></span><span class="label">Podcasts</span><span class="more">Read More</span></div>
<div class="abs media m2" role="img" aria-label="Open Bible photo for sermons"><span class="ico"></span><span class="label">Sermons</span><span class="more">Read More</span></div>
<div class="abs media m3" role="img" aria-label="Cross at sunset photo for videos"><span class="ico"></span><span class="label">Videos</span><span class="more">Read More</span></div>

<footer class="abs footer">
  <div class="abs f-h" style="left:103px;top:18px">Home Links</div>
  <ul class="abs f-list" style="left:103px;top:40px">
    <li>Home</li><li>About Us</li><li>Events</li><li>Prayer Request</li><li>Donate</li><li>Contact Us</li>
  </ul>
  <div class="abs f-h" style="left:248px;top:18px">Contact Info, Address &amp; Time</div>
  <div class="abs f-contact" style="left:248px;top:36px">
    <div><svg viewBox="0 0 10 10"><rect x="1" y="1" width="8" height="8" fill="none" stroke="#fff"/><rect x="3" y="3" width="4" height="2" fill="#fff"/></svg>555.201.4478</div>
    <div><svg viewBox="0 0 10 10"><rect x="0.5" y="1" width="9" height="6" fill="none" stroke="#fff"/><path d="M3 9h4" stroke="#fff"/></svg>www.harvestgateway.org</div>
    <div><svg viewBox="0 0 10 10"><path d="M5 9.5S1.5 6 1.5 4a3.5 3.5 0 0 1 7 0C8.5 6 5 9.5 5 9.5z" fill="#fff"/></svg>48 Orchard Lane, Millbrook NY 12545</div>
    <div><svg viewBox="0 0 10 10"><circle cx="5" cy="5.5" r="4" fill="none" stroke="#fff"/><path d="M5 3v3h2" stroke="#fff" fill="none"/></svg>9.00am -12.00am (Admission $20.00)</div>
  </div>
  <div class="abs f-h" style="left:420px;top:18px">Connect With US</div>
  <div class="abs social" style="left:420px;top:38px"><span></span><span></span><span></span><span></span><span></span></div>
  <div class="abs f-h" style="left:420px;top:65px">Payment options</div>
  <div class="abs cards" style="left:422px;top:78px"><span></span><span></span><span></span></div>
  <div class="abs donate-pill" style="left:421px;top:96px">Donate Online</div>
</footer>
<div class="abs f-legal">Privacy Policy | Terms Conditions | Sitemap | Contact Us<br>&copy; 2012 HGFM. All Rights Reserved</div>

</body>
</html>
```